MEDICAL CLINIC LETTERHEAD

Design is a letterhead for a non-profit medical center. The name of the clinic is VITARIDGE Community Health Center. Although the full name must be included, the community health center part is more of a description and should be less visible - i attached an example of what I mean by that (ATTACHED IMAGE IS AN EXAMPLE OF FONT SIZES NOT A DESIGN IDEA). Please design something modern, cool looking and unique because I can always download free templates.
Phone, email, website and etc will be added later.

Industry/Entity Type

MEDICAL

```html
<!DOCTYPE html>
<html lang="en">
<head>
<meta charset="utf-8">
<title>VITARIDGE Community Health Center – Letterhead</title>
<link rel="stylesheet" href="https://fonts.googleapis.com/css2?family=Montserrat:wght@400;600&family=Questrial&family=Open+Sans:wght@600&display=swap">
<style>
  :root {
    --paper: #ffffff;
    --ink-grey: #8f8f8f;
    --ink-dark: #444444;
    --brand-orange: #f7a731;
    --brand-green: #1b8a3c;
    --brand-blue: #27a4dd;
    --tint-orange: rgba(247, 167, 49, 0.10);
    --tint-green: rgba(27, 138, 60, 0.09);
    --tint-blue: rgba(39, 164, 221, 0.09);
    --signature-fill: #ececec;
  }
  * { margin: 0; padding: 0; box-sizing: border-box; }
  html, body { width: 908px; height: 1200px; overflow: hidden; background: var(--paper); }
  .letterhead {
    position: relative;
    width: 908px;
    height: 1200px;
    overflow: hidden;
    background: var(--paper);
    color: var(--ink-grey);
    font-family: "Questrial", sans-serif;
  }
  .brand { position: absolute; left: 32px; top: 96px; }
  .brand-name {
    font-family: "Montserrat", sans-serif; font-weight: 600;
    font-size: 27px; line-height: 1; color: var(--ink-dark); letter-spacing: -0.3px;
  }
  .brand-tagline {
    font-family: "Montserrat", sans-serif; font-weight: 400;
    font-size: 9.6px; color: var(--ink-dark); margin-top: 2px; letter-spacing: 0.3px;
  }
  .sender { position: absolute; left: 41px; top: 230px; font-family: "Montserrat", sans-serif; }
  .sender-name { font-weight: 600; font-size: 23.5px; color: var(--ink-grey); letter-spacing: 0.4px; line-height: 1; }
  .sender-line { font-size: 15.5px; line-height: 1; margin-top: 11px; letter-spacing: 0.6px; }
  .sender-address { font-size: 15px; line-height: 21px; margin-top: 10px; letter-spacing: 0.3px; }
  .letter-date {
    position: absolute; right: 43px; top: 344px;
    font-family: "Open Sans", sans-serif; font-weight: 600; font-size: 18.5px;
  }
  .letter-body {
    position: absolute; left: 36px; width: 829px;
    font-size: 17.2px; line-height: 19.7px; text-align: justify; hyphens: auto;
  }
  .p1 { top: 406px; }
  .p2 { top: 545px; }
  .p3 { top: 683px; }
  .signoff { position: absolute; left: 66px; top: 832px; font-size: 24px; }
  .signature {
    position: absolute; left: 86px; top: 880px; width: 165px; height: 98px;
    background: var(--signature-fill); border-radius: 4px;
  }
  .backdrop {
    position: absolute; left: 375px; top: 956px; width: 533px; height: 244px;
    background:
      radial-gradient(circle at 50% 20%, var(--tint-orange), transparent 45%),
      radial-gradient(circle at 15% 75%, var(--tint-green), transparent 40%),
      radial-gradient(circle at 90% 75%, var(--tint-blue), transparent 40%);
  }
  .contacts { position: absolute; left: 36px; top: 1076px; list-style: none; font-size: 15.5px; }
  .contacts li { display: flex; align-items: center; gap: 4px; height: 23.7px; }
  .contacts svg { width: 13px; height: 13px; flex: none; }
</style>
</head>
<body>
<main class="letterhead">
  <div class="backdrop" role="img" aria-label="Faint brand-colour decoration"></div>

  <header class="brand">
    <div class="brand-name">VITARIDGE</div>
    <div class="brand-tagline">COMMUNITY HEALTH CENTER</div>
  </header>

  <section class="sender">
    <h1 class="sender-name">CLARA MENDES</h1>
    <p class="sender-line">0198-765-432</p>
    <p class="sender-line">hello@northfieldcare.org</p>
    <p class="sender-address">5678 Harbor View Rd. Suite<br>456 Austin, TX 0000</p>
  </section>

  <p class="letter-date">12 December, 2023</p>

  <p class="letter-body p1">Lorem ipsum dolor sit amet, consectetuer adipiscing elit, sed diam nonummy nibh euismod tincidunt ut laoreet dolore magna aliquam erat volutpat. Ut wisi enim ad minim veniam, quis nostrud exerci tation ullamcorper suscipit lobortis nisl ut aliquip ex ea commodo consequat. Duis autem vel eum iriure dolor in hendrerit in vulputate velit esse molestie consequat, vel illum dolore eu feugiat nulla facilisis at vero eros et accumsan et iusto odio dignissim qui blandit praesent luptatum zzril delenit augue duis dolore te feugait nulla facilisi.</p>

  <p class="letter-body p2">Lorem ipsum dolor sit amet, cons ectetuer adipiscing elit, sed diam nonummy nibh euismod tincidunt ut laoreet dolore magna aliquam erat volutpat. Ut wisi enim ad minim veniam, quis nostrud exerci tation ullamcorper suscipit lobortis nisl ut aliquip ex ea commodo consequat.<br>Lorem ipsum dolor sit amet, consectetuer adipiscing elit, sed diam nonummy nibh euismod tincidunt ut laoreet dolore magna aliquam erat</p>

  <p class="letter-body p3">Lorem ipsum dolor sit amet, cons ectetuer adipiscing elit, sed diam nonummy nibh euismod tincidunt ut laoreet dolore magna aliquam erat volutpat. Ut wisi enim ad minim veniam, quis nostrud exerci tation ullamcorper suscipit lobortis nisl ut aliquip ex ea commodo consequat. Lorem ipsum dolor sit zamet, consectetuer adipiscing elit, sed diam nonummy nibh euismod tincidunt.</p>

  <p class="signoff">Managing Director</p>
  <div class="signature" role="img" aria-label="Handwritten signature of the managing director"></div>

  <ul class="contacts">
    <li>
      <svg viewBox="0 0 12 12" aria-hidden="true"><circle cx="6" cy="6" r="6" fill="var(--brand-orange)"/><path d="M4 3.2l1 1.3-.6.8c.4.9 1.1 1.6 2 2l.8-.6 1.3 1-.6 1c-2.3-.2-4.3-2.2-4.5-4.5z" fill="#fff"/></svg>
      0198-765-432
    </li>
    <li>
      <svg viewBox="0 0 12 12" aria-hidden="true"><circle cx="6" cy="6" r="6" fill="var(--brand-green)"/><rect x="3" y="4" width="6" height="4.2" fill="none" stroke="#fff" stroke-width="0.9"/><path d="M3 4l3 2.3L9 4" fill="none" stroke="#fff" stroke-width="0.9"/></svg>
      info@vitaridge.org
    </li>
    <li>
      <svg viewBox="0 0 12 12" aria-hidden="true"><circle cx="6" cy="6" r="6" fill="var(--brand-blue)"/><circle cx="6" cy="6" r="3.3" fill="none" stroke="#fff" stroke-width="0.8"/><ellipse cx="6" cy="6" rx="1.4" ry="3.3" fill="none" stroke="#fff" stroke-width="0.8"/><path d="M2.7 6h6.6" stroke="#fff" stroke-width="0.8"/></svg>
      www.vitaridge.org
    </li>
  </ul>
</main>
</body>
</html>
```